High Tech Real Estate Startup needs a business card

We are developing an innovative real estate marketing product based around advanced search and virtual reality.

We talk to people, we need business cards.

Target Market(s)

The target market is technology professionals and realtors.

Contact Information for Business Card

The information to be included will include

Name
Title
Phone Number
E-mail Address
www.zelquin.com

It should use simple iconography for each one of those fields.

Font styles to use
Other font styles liked:
• Co, Jubilat, Avenir

Colors

Designer to choose colors to be used in the design.

Requirements
Must have
• Clean aesthetic,
• Good use of negative space.
• It should use our company logo, shown in the attached file. It is able to use the negative of that logo (coloured font and white background) and I have attached other acceptable accent colours in a swatch file.
Should not have
• Should not be too busy
• No extraneous text (slogans, tag lines etc)

```html
<!DOCTYPE html>
<html lang="en">
<head>
<meta charset="utf-8">
<title>Zelquin Business Card</title>
<link rel="stylesheet" href="https://fonts.googleapis.com/css2?family=Montserrat:wght@500&family=Open+Sans:wght@400;600&display=swap">
<style>
  :root {
    --backdrop: #3a3a3c;
    --card: #1e1f21;
    --emboss: #2f3033;
    --teal: #45b8bd;
    --ink: #f2f2f2;
    --ink-soft: #c9c9c9;
  }
  * { margin: 0; padding: 0; box-sizing: border-box; }
  html, body {
    width: 799px; height: 1200px; overflow: hidden;
    background: var(--backdrop);
  }
  .sheet {
    width: 799px; height: 1200px;
    display: flex; flex-direction: column; align-items: center; justify-content: space-around;
  }
  .card {
    position: relative;
    width: 700px; height: 400px;
    background: var(--card);
    border-radius: 34px;
    overflow: hidden;
  }
  .card-front .wordmark {
    position: absolute; inset: 0;
    display: flex; align-items: center; justify-content: center;
    font-family: "Montserrat", sans-serif; font-weight: 500;
    font-size: 82px; letter-spacing: 6px;
    color: var(--emboss);
  }
  .card-back .accent-dot {
    position: absolute; left: -34px; top: 38px;
    width: 68px; height: 68px; border-radius: 50%;
    background: var(--teal);
  }
  .holder { position: absolute; left: 58px; top: 44px; font-family: "Open Sans", sans-serif; }
  .holder .name { font-size: 28px; font-weight: 600; color: var(--ink); }
  .holder .title { font-size: 15px; color: var(--ink-soft); margin-top: 2px; }
  .card-back .wordmark {
    position: absolute; right: 50px; top: 178px;
    font-family: "Montserrat", sans-serif; font-weight: 500;
    font-size: 62px; letter-spacing: 4px; color: var(--teal);
  }
  .contacts {
    position: absolute; left: 40px; bottom: 46px;
    list-style: none; font-family: "Open Sans", sans-serif;
    font-size: 16px; color: var(--ink);
  }
  .contacts li { display: flex; align-items: center; gap: 10px; height: 26px; }
  .contacts svg { width: 16px; height: 16px; flex: none; }
  .contacts .no-icon { padding-left: 26px; }
</style>
</head>
<body>
<main class="sheet">
  <section class="card card-front">
    <div class="wordmark">ZELQUIN</div>
  </section>

  <section class="card card-back">
    <span class="accent-dot"></span>
    <div class="holder">
      <p class="name">John Doe Smith</p>
      <p class="title">Managing Director</p>
    </div>
    <div class="wordmark">ZELQUIN</div>
    <ul class="contacts">
      <li>
        <svg viewBox="0 0 16 16"><circle cx="8" cy="8" r="8" fill="#f2f2f2"/><path d="M5 4.5h2l.6 2-1 .8a5 5 0 0 0 2.1 2.1l.8-1 2 .6v2c-3.6.3-6.8-2.9-6.5-6.5z" fill="#1e1f21"/></svg>
        <span>555.555.5555</span>
      </li>
      <li>
        <svg viewBox="0 0 16 16"><circle cx="8" cy="8" r="8" fill="#f2f2f2"/><rect x="4" y="5" width="8" height="6" rx="1" fill="#1e1f21"/><path d="M4.3 5.4 8 8.3l3.7-2.9" stroke="#f2f2f2" stroke-width=".9" fill="none"/></svg>
        <span>johndoe@zelquin.com</span>
      </li>
      <li>
        <svg viewBox="0 0 16 16"><circle cx="8" cy="8" r="8" fill="#f2f2f2"/><circle cx="8" cy="8" r="4.2" fill="none" stroke="#1e1f21" stroke-width="1"/><path d="M3.8 8h8.4M8 3.8c-2 2.5-2 5.9 0 8.4M8 3.8c2 2.5 2 5.9 0 8.4" stroke="#1e1f21" stroke-width=".9" fill="none"/></svg>
        <span>www.zelquin.com</span>
      </li>
    </ul>
  </section>
</main>
</body>
</html>
```